Job Recruiting Agemcy

almost like my current site www.plorvex.com but with these changes see and what i meant about the across the to the site says home job companies categories pages blog and login sign up that should only be the 4 i said only 1 home 2 industries 3 jobs 4 contact us. and remove latest blog post and our partners because that's not us we have to post acuarte information thanks and the name of the company if your using is is work and careful hiring partners and want it easy for us to post and remove jobs and where it emails us every resume or person that applies

Requirements
Must have
• must send email to us when an application is submitted and try to incorparate the colors of current site
Nice to have
• i want a pretty basic site for now just like the one i have but with all thats above were its easy for me being the own to be able to post jobs and everything

```html
<!DOCTYPE html>
<html lang="en">
<head>
<meta charset="utf-8">
<title>Plorvex – Work and careful hiring partners</title>
<link href="https://fonts.googleapis.com/css2?family=Roboto:ital,wght@0,400;0,500;0,700;1,400&display=swap" rel="stylesheet">
<style>
:root{
  --green:#4b7d5f;
  --green-dark:#3f6d52;
  --red:#e15a61;
  --ink:#111;
  --muted:#666;
  --card:#f4f4f4;
  --white:#fff;
}
*{box-sizing:border-box;margin:0;padding:0}
html,body{width:1200px;height:3378px;overflow:hidden}
body{font-family:'Roboto',sans-serif;color:var(--ink);background:#fff;position:relative}
.abs{position:absolute}
a{color:inherit;text-decoration:none}

/* header */
.site-header{position:absolute;left:0;top:0;width:1200px;height:184px;background:var(--green)}
.brand{position:absolute;left:112px;top:60px;display:flex;align-items:center;gap:8px}
.brand-mark{width:14px;height:14px;background:var(--red);border-radius:50%}
.brand-name{font-weight:700;font-size:24px;color:var(--red);letter-spacing:1px}
.brand-tag{position:absolute;left:112px;top:96px;font-size:8px;color:#222;font-weight:500;text-transform:uppercase}
.contact-item{position:absolute;top:28px;display:flex;gap:12px;color:#fff}
.contact-icon{width:40px;height:40px;border-radius:50%;background:var(--red);display:flex;align-items:center;justify-content:center;margin-top:3px}
.contact-label{font-size:15px;font-weight:500}
.contact-value{font-size:20px;font-weight:700;margin-top:2px}
.divider-v{position:absolute;left:764px;top:26px;width:2px;height:48px;background:#fff}
.main-nav{position:absolute;left:421px;top:122px;display:flex;gap:38px;font-size:15px;font-weight:700;color:#fff}
.main-nav .active{color:var(--red);border-bottom:2px solid var(--red);padding-bottom:8px}
.btn-outline{position:absolute;top:105px;height:54px;border:3px solid #fff;border-radius:27px;color:#fff;font-weight:700;font-size:15px;display:flex;align-items:center;justify-content:center;gap:8px}

/* hero */
.hero{position:absolute;left:0;top:184px;width:1200px;height:638px;background:linear-gradient(100deg,#8c8f94 0%,#a6a9ad 35%,#c6c8ca 60%,#e0e0de 100%)}
.hero-kicker{position:absolute;left:788px;top:200px;transform:translateX(-50%);font-size:20px;font-weight:700;color:#fff;white-space:nowrap}
.hero-title{position:absolute;left:788px;top:236px;transform:translateX(-50%);font-size:42px;font-weight:700;color:#fff;white-space:nowrap}
.search-bar{position:absolute;left:459px;top:310px;width:658px;height:56px;background:#fff;border-radius:28px;display:flex;overflow:hidden}
.search-field{width:236px;border-right:1px solid #ddd;padding-left:37px;display:flex;align-items:center;font-size:14px;color:#555}
.search-btn{flex:1;background:var(--green);color:#fff;font-weight:700;font-size:14px;display:flex;align-items:center;justify-content:center}
.dots{position:absolute;left:580px;top:571px;display:flex;gap:4px}
.dots span{width:12px;height:12px;border:2px solid #fff;border-radius:50%}
.dots .on{background:#fff}

/* intro */
.intro{position:absolute;left:0;top:888px;width:1200px;text-align:center;font-size:24px;font-weight:500;line-height:34px}
.section-sub{position:absolute;left:0;top:1018px;width:1200px;text-align:center;font-size:26px;font-weight:700;color:var(--green)}
.industry{position:absolute;top:1094px;width:231px;height:219px;background:var(--card);text-align:center}
.industry-icon{width:88px;height:88px;border-radius:50%;background:var(--red);margin:25px auto 0;display:flex;align-items:center;justify-content:center}
.industry-name{margin-top:14px;font-size:14px;font-weight:700;color:var(--green);line-height:24px;padding:0 20px}

/* recent jobs */
.jobs{position:absolute;left:0;top:1408px;width:1200px;height:652px;background:linear-gradient(90deg,#467559,#4f8264 50%,#467559)}
.section-title{position:absolute;left:0;width:1200px;text-align:center;font-size:35px;font-weight:700}
.title-rule{position:absolute;left:569px;width:62px;height:3px;background:var(--green)}
.job-photo{position:absolute;top:146px;width:470px;height:310px;border:3px solid #fff}
.job-card{position:absolute;top:342px;width:378px;height:227px;background:#fff;text-align:center}
.job-card h3{margin-top:24px;font-size:27px;font-weight:500;color:var(--green)}
.job-card p{margin:14px auto 0;width:310px;font-size:14px;line-height:26px;color:var(--muted)}
.btn-red{display:inline-flex;align-items:center;justify-content:center;gap:5px;width:165px;height:44px;border-radius:22px;background:var(--red);color:#fff;font-size:14px;font-weight:700;margin-top:12px}

/* testimonials */
.t-card{position:absolute;top:2235px;width:606px;height:270px;left:297px;background:#fff;box-shadow:0 4px 18px rgba(0,0,0,.12);text-align:center}
.t-side{position:absolute;top:2235px;height:295px;background:#fff;box-shadow:0 4px 18px rgba(0,0,0,.06);font-style:italic;font-size:14px;line-height:26px;color:#bbb;overflow:hidden}
.stars{margin-top:30px;color:var(--red);font-size:16px;letter-spacing:2px}
.quote{margin:10px auto 0;width:492px;font-size:14px;font-style:italic;line-height:26px;color:#666;text-align:justify;text-align-last:center}
.quote-author{margin-top:8px;font-size:17px;color:var(--red)}
.avatar{position:absolute;left:554px;top:2476px;width:92px;height:92px;border-radius:50%;border:4px solid #fff;background:linear-gradient(#d8d4cf,#9d9892)}
.arrow-btn{position:absolute;top:2373px;width:46px;height:46px;border-radius:50%;background:var(--green);display:flex;align-items:center;justify-content:center}

/* call to action */
.cta{position:absolute;left:0;top:2657px;width:1200px;height:286px;background:linear-gradient(90deg,#d7646b,#e56f75 50%,#e4686e)}
.cta-person{position:absolute;left:862px;top:2608px;width:250px;height:335px;background:linear-gradient(#e8e0d2,#b9c9e0);border-radius:120px 120px 0 0}
.cta h2{position:absolute;left:0;top:72px;width:1200px;text-align:center;color:#fff;font-size:35px;font-weight:700}
.cta p{position:absolute;left:0;top:124px;width:1200px;text-align:center;color:#fff;font-size:14px}
.btn-green{position:absolute;top:163px;width:164px;height:44px;border-radius:22px;background:var(--green);color:#fff;font-size:14px;font-weight:700;display:flex;align-items:center;justify-content:center}

/* footer */
.f-head{position:absolute;top:3033px;font-size:22px;font-weight:700}
.f-text{font-size:15px;color:#555;line-height:26px}
.f-links{position:absolute;left:421px;top:3082px;font-size:15px;color:#555;line-height:39px}
.f-contact{position:absolute;left:587px;font-size:15px;color:#555;display:flex;gap:14px;line-height:30px}
.sub-input{position:absolute;left:828px;top:3076px;width:261px;height:44px;border:1px solid #ccc;font-size:14px;color:#777;padding-left:15px;display:flex;align-items:center}
.sub-btn{position:absolute;left:828px;top:3127px;width:261px;height:44px;background:var(--red);color:#fff;font-size:13px;font-weight:700;letter-spacing:3px;display:flex;align-items:center;justify-content:center}
.social{position:absolute;top:3203px;width:42px;height:42px;border-radius:50%}
.f-rule{position:absolute;left:110px;top:3298px;width:980px;height:1px;background:#ccc}
.copyright{position:absolute;left:0;top:3330px;width:1200px;text-align:center;font-size:14px;color:#333}
</style>
</head>
<body>

<header class="site-header">
  <div class="brand"><span class="brand-mark"></span><span class="brand-name">PLORVEX</span></div>
  <div class="brand-tag">Servicing you since 1990</div>

  <div class="contact-item" style="left:520px">
    <span class="contact-icon"><svg width="16" height="16" viewBox="0 0 24 24" fill="#fff"><path d="M6.6 10.8a15 15 0 006.6 6.6l2.2-2.2a1 1 0 011-.25 11.4 11.4 0 003.6.6 1 1 0 011 1V20a1 1 0 01-1 1A17 17 0 013 4a1 1 0 011-1h3.5a1 1 0 011 1 11.4 11.4 0 00.6 3.6 1 1 0 01-.25 1z"/></svg></span>
    <div><div class="contact-label">Call us Today :</div><div class="contact-value">+1 555 014 2280</div></div>
  </div>
  <div class="divider-v"></div>
  <div class="contact-item" style="left:812px">
    <span class="contact-icon"><svg width="16" height="14" viewBox="0 0 24 20" fill="#fff"><path d="M2 2h20v2l-10 7L2 4z"/><path d="M2 7l10 7 10-7v11H2z"/></svg></span>
    <div><div class="contact-label">Mail us Today :</div><div class="contact-value">hello@plorvex.com</div></div>
  </div>

  <nav class="main-nav">
    <a class="active">Home</a><a>Industries</a><a>Jobs</a><a>Contact us</a>
  </nav>
  <a class="btn-outline" style="left:806px;width:130px"><svg width="11" height="13" viewBox="0 0 12 14" fill="#fff"><circle cx="6" cy="4" r="3.5"/><path d="M0 14c0-4 2.5-6 6-6s6 2 6 6z"/></svg>LOGIN</a>
  <a class="btn-outline" style="left:961px;width:130px">SIGNUP</a>
</header>

<section class="hero" role="img" aria-label="Photo of a smiling man in a suit with job candidates holding papers in an office">
  <div class="hero-kicker">Search from 0 job offers</div>
  <div class="hero-title">Your career starts here!</div>
  <div class="search-bar">
    <div class="search-field">Keywords</div>
    <div class="search-field">Location</div>
    <div class="search-btn">SEARCH</div>
  </div>
  <div class="dots"><span></span><span class="on"></span><span></span></div>
</section>

<section>
  <p class="intro">We have over 35 years of Specialized Recruiting and souring experience.<br>We cover a broad spectrum of industries to include some of the top<br>aerospace and pharmaceutical commercial companies of today.</p>
  <h2 class="section-sub">INDUSTRIES WE SUPPORT</h2>

  <div class="industry" style="left:111px">
    <div class="industry-icon"><svg width="48" height="48" viewBox="0 0 48 48" fill="none" stroke="#fff" stroke-width="2"><circle cx="24" cy="14" r="6"/><circle cx="12" cy="20" r="4"/><circle cx="36" cy="20" r="4"/><path d="M16 40V30a8 8 0 0116 0v10"/></svg></div>
    <div class="industry-name">Aero Space- Northwind Aero Controls, Orbitra, Voltline Electric</div>
  </div>
  <div class="industry" style="left:360px">
    <div class="industry-icon"><svg width="48" height="48" viewBox="0 0 48 48" fill="none" stroke="#fff" stroke-width="2"><rect x="8" y="20" width="32" height="20"/><path d="M12 20V12h24v8M14 28h4M22 28h4M30 28h4M14 34h4M22 34h4M30 34h4"/></svg></div>
    <div class="industry-name">Pharmaceutical/ Biotechnology Cellora Labs , Petal &amp; Co.</div>
  </div>
  <div class="industry" style="left:609px">
    <div class="industry-icon"><svg width="50" height="48" viewBox="0 0 50 48" fill="none" stroke="#fff" stroke-width="2"><rect x="6" y="14" width="26" height="20"/><path d="M32 20h8l6 7v7H32z"/><circle cx="14" cy="36" r="3"/><circle cx="38" cy="36" r="3"/><path d="M13 24l4 4 8-8"/></svg></div>
    <div class="industry-name">Transportation- Ridgeway Freight, Parcelio</div>
  </div>
  <div class="industry" style="left:858px">
    <div class="industry-icon"><svg width="48" height="48" viewBox="0 0 48 48" fill="none" stroke="#fff" stroke-width="2"><rect x="6" y="10" width="36" height="26"/><path d="M18 42h12M24 36v6"/><circle cx="24" cy="20" r="4"/><path d="M16 32a8 8 0 0116 0"/></svg></div>
    <div class="industry-name">Medical - Medrin, Carewell</div>
  </div>
</section>

<section class="jobs">
  <h2 class="section-title" style="top:64px;color:#fff">RECENT JOBS</h2>
  <div class="title-rule" style="top:116px;background:#fff"></div>

  <div class="job-photo" style="left:109px;background:linear-gradient(135deg,#d9d4cc,#f2f0ec 50%,#3a3f4a)" role="img" aria-label="Photo of two people shaking hands over paperwork on a desk"></div>
  <div class="job-card" style="left:155px">
    <h3>Lorem ipsum dolor sit</h3>
    <p>Nemo enim ipsam voluptatem quia voluptas sit aspernatur aut odit aut fugit, sed quia cons equuntur magni dolores eos qui</p>
    <a class="btn-red">LEARN MORE <svg width="12" height="12" viewBox="0 0 12 12"><circle cx="6" cy="6" r="6" fill="#fff"/><path d="M5 3l3 3-3 3" stroke="#e15a61" stroke-width="1.8" fill="none"/></svg></a>
  </div>

  <div class="job-photo" style="left:620px;background:linear-gradient(135deg,#cfd3d8,#f3f3f3 45%,#1f2535)" role="img" aria-label="Photo of a person signing a document next to a laptop"></div>
  <div class="job-card" style="left:666px">
    <h3>Lorem ipsum dolor sit</h3>
    <p>Nemo enim ipsam voluptatem quia voluptas sit aspernatur aut odit aut fugit, sed quia cons equuntur magni dolores eos qui</p>
    <a class="btn-red">LEARN MORE <svg width="12" height="12" viewBox="0 0 12 12"><circle cx="6" cy="6" r="6" fill="#fff"/><path d="M5 3l3 3-3 3" stroke="#e15a61" stroke-width="1.8" fill="none"/></svg></a>
  </div>
</section>

<section>
  <h2 class="section-title" style="top:2148px">TESTIMONIALS</h2>
  <div class="title-rule" style="top:2200px"></div>

  <div class="t-side" style="left:-40px;width:252px;padding:80px 58px 0 40px;text-align:right">t, sed do eiusmod tempor minim veniam, quis nostrud consequat. Duis aute irure dolore eu fugiat</div>
  <div class="t-side" style="left:983px;width:260px;padding:80px 0 0 58px">"Lorem ipsum dolor sit amet incididunt ut labore et dolore exercitation ullamco laboris reprehenderit in voluptate</div>

  <div class="t-card">
    <div class="stars">★★★★★</div>
    <p class="quote">"I was highly impressed by the professionalism shown during my interview process. It was less an interview and more of a conversation with the recruiter. I felt comfortable sharing my previous management experience and all of my qualifications for the Operations Manager position. I was informed about Harbor Dental Group' History, Mission and Values with pride and enthusiasm."</p>
    <div class="quote-author">Mara Quillan, - CEO in Company Name</div>
  </div>
  <div class="avatar" role="img" aria-label="Portrait photo of the reviewer"></div>

  <div class="arrow-btn" style="left:78px"><svg width="14" height="14" viewBox="0 0 14 14"><path d="M9 2L4 7l5 5" stroke="#fff" stroke-width="2" fill="none"/></svg></div>
  <div class="arrow-btn" style="left:1070px"><svg width="14" height="14" viewBox="0 0 14 14"><path d="M5 2l5 5-5 5" stroke="#fff" stroke-width="2" fill="none"/></svg></div>
</section>

<section class="cta" role="img" aria-label="Faint photo of people working at a table under a coral overlay">
  <h2>SEEKING FOR A JOB?</h2>
  <p>Browse hundreds of job offers and find the best suitable position.</p>
  <a class="btn-green" style="left:429px">SEARCH JOBS</a>
  <a class="btn-green" style="left:607px">ADD A RESUME</a>
</section>
<div class="cta-person" role="img" aria-label="Photo of a smiling woman with glasses and folded arms"></div>

<footer>
  <h4 class="f-head" style="left:108px">Plorvex</h4>
  <p class="f-text abs" style="left:110px;top:3080px;width:270px">Lorem ipsum dolor sit amet, conse ctetur adipiscing elit, sed do eiusmod tempor incididunt ut labore</p>

  <h4 class="f-head" style="left:417px">Useful Links</h4>
  <div class="f-links">Home,<br>Industries,<br>Jobs<br>Contact us</div>

  <h4 class="f-head" style="left:587px">Contact</h4>
  <div class="f-contact" style="top:3077px"><svg width="13" height="13" viewBox="0 0 24 24" fill="#e15a61" style="margin-top:5px"><path d="M6.6 10.8a15 15 0 006.6 6.6l2.2-2.2a1 1 0 011-.25 11.4 11.4 0 003.6.6 1 1 0 011 1V20a1 1 0 01-1 1A17 17 0 013 4a1 1 0 011-1h3.5a1 1 0 011 1 11.4 11.4 0 00.6 3.6 1 1 0 01-.25 1z"/></svg><span>+1 555 014 2280</span></div>
  <div class="f-contact" style="top:3139px"><svg width="14" height="12" viewBox="0 0 24 20" fill="#e15a61" style="margin-top:6px"><path d="M2 2h20v2l-10 7L2 4z"/><path d="M2 7l10 7 10-7v11H2z"/></svg><span>hello@plorvex.com</span></div>
  <div class="f-contact" style="top:3201px"><svg width="10" height="14" viewBox="0 0 10 14" fill="#e15a61" style="margin-top:6px"><path d="M5 0a5 5 0 015 5c0 4-5 9-5 9S0 9 0 5a5 5 0 015-5z"/><circle cx="5" cy="5" r="2" fill="#fff"/></svg><span>18 Linden Row, Suite 4<br>Brookfield, ST 20410 USA</span></div>

  <h4 class="f-head" style="left:826px">Subscribe</h4>
  <div class="sub-input">Email Address</div>
  <div class="sub-btn">SUBSCRIBE US</div>
  <span class="social" style="left:868px;background:var(--green)"></span>
  <span class="social" style="left:914px;background:var(--green)"></span>
  <span class="social" style="left:961px;background:var(--red)"></span>
  <span class="social" style="left:1007px;background:var(--green)"></span>

  <div class="f-rule"></div>
  <p class="copyright">© Copyright 2020 Company name | All Rights Reserved.</p>
</footer>

</body>
</html>
```